Veltra Cosmi Holdings Limited is a asset management company and project funding company, we specialise in high end finance for high net worth individuals, we are looking for a new logo letterhead template, email footer template and business card design. The letterhead template should be designed in word format so that the letterheading can be used electronically.

Below is the current logo that is a but plain and a little cheaper looking, colour schemes are not important just that it looks professional.

I am looking for a sharp impact that stands out,

Target Market(s)

High net worth individuals and institutions

Industry/Entity Type

Finance

Contact Information for Business Card

Veltra Cosmi Holdings Limited
T: 0333 418 2965

M: 07631 490718
E:derek.holm@veltra-cosmiholdings.com

REEDWATER COVE, EAST HARBOUR ROAD
FIFTH FLOOR, SUITE 512
P.O. BOX CB-47316
NASSAU BAHAMAS

Logo Text

Font styles to use
Serif
Sans Serif
Script
Other font styles liked:
• Tahoma

Colors
fbed22
6b449b
ec1f27
f78f20
33b8a4
0592cd

Requirements
Must have
• Colours schemes would look good in blue’s green’s purples.

Yellow and Purple together maybe a nice combination.
Nice to have
• I want the log to look sharpe, relate to a global presence, but I also want to it to look established.
Should not have
• N/a

```html
<!DOCTYPE html>
<html lang="en">
<head>
<meta charset="utf-8">
<title>Veltra Cosmi Holdings Limited — Stationery</title>
<link rel="stylesheet" href="https://fonts.googleapis.com/css2?family=Open+Sans:wght@400;600&family=Rubik:wght@700&display=swap">
<style>
  :root {
    --green: #3db52f;
    --purple: #6b449b;
    --purple-soft: #e9e4f2;
    --ink: #000000;
    --paper: #ffffff;
    --paper-edge: #e6e6e6;
    --stage-light: #ebebeb;
    --stage-warm: #d9d3ca;
    --slate-top: #3a4750;
    --slate-bottom: #1f2a31;
    --text-dark: #222222;
    --text-light: #ffffff;
  }
  * { box-sizing: border-box; margin: 0; padding: 0; }
  html, body { width: 1200px; height: 2508px; overflow: hidden; }
  body { font-family: "Open Sans", Tahoma, sans-serif; background: var(--stage-light); }

  .section { position: relative; width: 1200px; overflow: hidden; }
  .wordmark { font-family: "Rubik", Tahoma, sans-serif; font-weight: 700; text-transform: uppercase; line-height: 1.05; }
  .brand-ring { border-radius: 50%; border-style: solid; }

  /* Letterhead */
  .letterhead-stage { height: 766px; background: var(--stage-warm); }
  .letterhead {
    position: absolute; left: 370px; top: 50px; width: 470px; height: 665px;
    background: var(--paper); box-shadow: 0 6px 18px rgba(0,0,0,.18);
  }
  .letterhead .head { position: absolute; left: 30px; top: 30px; display: flex; align-items: center; gap: 10px; }
  .letterhead .head .brand-ring { width: 34px; height: 34px; border-width: 3px; border-color: var(--purple); }
  .letterhead .head .wordmark { font-size: 13px; color: var(--text-dark); width: 150px; }
  .letterhead .contacts { position: absolute; right: 30px; top: 34px; display: grid; grid-template-columns: auto auto; gap: 4px 22px; font-size: 7.5px; color: var(--text-dark); }
  .letterhead .contacts span { display: flex; align-items: center; gap: 4px; }
  .letterhead .contacts i { width: 6px; height: 6px; background: var(--text-dark); border-radius: 1px; display: inline-block; }
  .letterhead .faint-ring { position: absolute; left: 95px; top: 170px; width: 280px; height: 280px; border: 16px solid var(--purple-soft); border-radius: 50%; }
  .letterhead .corner { position: absolute; left: 0; bottom: 0; width: 470px; height: 200px; }

  /* Business cards */
  .cards-stage { height: 790px; background: var(--stage-light); }
  .card {
    position: absolute; top: 275px; width: 420px; height: 240px;
    background: var(--ink); box-shadow: 0 10px 24px rgba(0,0,0,.28);
  }
  .card-back { left: 150px; }
  .card-front { left: 630px; display: flex; align-items: center; justify-content: center; gap: 16px; }
  .card-front .brand-ring { width: 58px; height: 58px; border-width: 5px; border-color: var(--purple); }
  .card-front .wordmark { font-size: 22px; color: var(--green); width: 190px; }
  .card-back .wordmark { position: absolute; left: 28px; top: 30px; font-size: 17px; color: var(--green); width: 200px; }
  .card-back .details { position: absolute; left: 28px; top: 100px; list-style: none; font-size: 10px; color: var(--green); line-height: 1.45; }
  .card-back .details li { display: flex; gap: 8px; align-items: flex-start; }
  .card-back .details svg { flex: none; margin-top: 2px; }

  /* Email footer */
  .email-footer { height: 404px; background: var(--ink); margin-top: 8px; }
  .email-footer .brand { position: absolute; left: 100px; top: 70px; width: 290px; text-align: center; }
  .email-footer .brand .brand-ring { width: 150px; height: 150px; border-width: 6px; border-color: var(--purple); margin: 0 auto 22px; }
  .email-footer .brand .wordmark { font-size: 34px; color: var(--green); }
  .email-footer .signature { position: absolute; right: 40px; top: 72px; text-align: right; color: var(--text-light); }
  .email-footer .signature .wordmark { font-size: 34px; letter-spacing: .5px; }
  .email-footer .signature .wordmark small { display: block; font-size: 15px; letter-spacing: 3.5px; margin-top: 4px; }
  .contact-list { list-style: none; margin-top: 16px; }
  .contact-list li { display: flex; justify-content: flex-end; align-items: center; gap: 12px; height: 41px; font-size: 17px; }
  .contact-list .icon { width: 30px; height: 30px; background: var(--text-light); display: flex; align-items: center; justify-content: center; }
  .social-row { position: absolute; left: 536px; top: 286px; display: flex; align-items: center; gap: 8px; width: 624px; }
  .social-row .social { width: 36px; height: 36px; background: var(--text-light); border-radius: 3px; flex: none; }
  .social-row .rule { flex: 1; border-top: 3px dashed var(--text-light); margin-left: 4px; }

  /* Logo presentation */
  .logo-stage { height: 538px; background: radial-gradient(ellipse at 60% 30%, var(--slate-top), var(--slate-bottom)); margin-top: 2px; }
  .logo-stage .brand { position: absolute; left: 0; right: 0; top: 60px; text-align: center; }
  .logo-stage .brand .brand-ring { width: 280px; height: 280px; border-width: 8px; border-color: var(--purple); margin: 0 auto 28px; }
  .logo-stage .brand .wordmark { font-size: 58px; color: var(--green); }
</style>
</head>
<body>

<section class="section letterhead-stage">
  <article class="letterhead">
    <header class="head">
      <div class="brand-ring"></div>
      <div class="wordmark">Veltra Cosmi Holdings Limited</div>
    </header>
    <div class="contacts">
      <span><i></i>0333 418 2965</span>
      <span><i></i>derek.holm@veltra-cosmiholdings.com</span>
      <span><i></i>07631 490718</span>
      <span><i></i>www.veltracosmi-example.com.au</span>
    </div>
    <div class="faint-ring"></div>
    <svg class="corner" viewBox="0 0 470 200" preserveAspectRatio="none">
      <polygon points="0,60 200,150 0,150" fill="var(--green)"/>
      <polygon points="0,150 200,150 470,100 470,200 0,200" fill="var(--purple)"/>
      <polygon points="0,60 200,150 0,150" fill="var(--green)"/>
    </svg>
  </article>
</section>

<section class="section cards-stage">
  <article class="card card-back">
    <div class="wordmark">Veltra Cosmi Holdings Limited</div>
    <ul class="details">
      <li>
        <svg width="9" height="11" viewBox="0 0 9 11"><path d="M4.5 0a4 4 0 0 1 4 4c0 3-4 7-4 7s-4-4-4-7a4 4 0 0 1 4-4z" fill="var(--green)"/></svg>
        <span>REEDWATER COVE, EAST HARBOUR ROAD<br>FIFTH FLOOR, SUITE 512<br>P.O. BOX CB-47316<br>NASSAU BAHAMAS</span>
      </li>
      <li>
        <svg width="9" height="10" viewBox="0 0 9 10"><path d="M1 0h2l1 3-1.5 1a6 6 0 0 0 3 3L6.5 5.5l3 1v2l-1 1C4 9 0 5 0 1z" fill="var(--green)"/></svg>
        <span>0333 418 2965</span>
      </li>
      <li>
        <svg width="9" height="10" viewBox="0 0 9 10"><rect x="1" y="0" width="7" height="10" rx="1" fill="var(--green)"/></svg>
        <span>07631 490718</span>
      </li>
      <li>
        <svg width="9" height="10" viewBox="0 0 9 10"><rect x="0" y="2" width="9" height="6" fill="var(--green)"/></svg>
        <span>derek.holm@veltra-cosmiholdings.com</span>
      </li>
      <li>
        <svg width="9" height="10" viewBox="0 0 9 10"><circle cx="4.5" cy="5" r="4.5" fill="var(--green)"/></svg>
        <span>www.veltracosmi-example.com.au</span>
      </li>
    </ul>
  </article>
  <article class="card card-front">
    <div class="brand-ring"></div>
    <div class="wordmark">Veltra Cosmi Holdings Limited</div>
  </article>
</section>

<section class="section email-footer">
  <div class="brand">
    <div class="brand-ring"></div>
    <div class="wordmark">Veltra Cosmi Holdings Limited</div>
  </div>
  <div class="signature">
    <div class="wordmark">Veltra Cosmi<small>Holdings Limited</small></div>
    <ul class="contact-list">
      <li>0333 418 2965
        <span class="icon"><svg width="18" height="18" viewBox="0 0 18 18"><path d="M3 1h3l2 5-2 1.5a10 10 0 0 0 4.5 4.5L12 10l5 2v3l-2 2C8 17 1 10 1 3z" fill="var(--ink)"/></svg></span>
      </li>
      <li>07631 490718
        <span class="icon"><svg width="18" height="20" viewBox="0 0 18 20"><rect x="4" y="1" width="10" height="18" rx="2" fill="none" stroke="var(--ink)" stroke-width="2"/><circle cx="9" cy="16" r="1.2" fill="var(--ink)"/></svg></span>
      </li>
      <li>derek.holm@veltra-cosmiholdings.com
        <span class="icon"><svg width="20" height="14" viewBox="0 0 20 14"><rect x="1" y="1" width="18" height="12" fill="none" stroke="var(--ink)" stroke-width="2"/><path d="M1 1l9 7 9-7" fill="none" stroke="var(--ink)" stroke-width="2"/></svg></span>
      </li>
      <li>www.veltracosmi-example.com.au
        <span class="icon"><svg width="20" height="20" viewBox="0 0 20 20"><circle cx="10" cy="10" r="9" fill="var(--ink)"/><circle cx="10" cy="10" r="4" fill="var(--text-light)"/></svg></span>
      </li>
    </ul>
  </div>
  <div class="social-row">
    <span class="social"></span>
    <span class="social"></span>
    <span class="social"></span>
    <span class="social"></span>
    <span class="rule"></span>
  </div>
</section>

<section class="section logo-stage">
  <div class="brand">
    <div class="brand-ring"></div>
    <div class="wordmark">Veltra Cosmi Holdings Limited</div>
  </div>
</section>

</body>
</html>
```